Redesign Canvas Art E-Commerce Website

Help! I hired a couple of companies on Brisklo.com to build and design an e-commerce website for me. After three long and painful months, I have one that I believe is functional on the back-end, but aesthetically on the front end is a mess.

We are a small family business that will take your digital photo and manipulate it into a digitally created oil, watercolor or impressionist style pieces of artwork that we print on museum quality, gallery grade canvas and ship to the customer, ready to hang.

We are looking to create an e-commerce website where a customer can choose their art style, upload a photo, choose their canvas size and orientation (horizontal or vertical) and checkout. Within 48 hours, we will send them back a proof of their newly created, customized artwork for them to approve or not approve. If they approve, we print, package and ship them the product. If they do not approve, we offer unlimited revisions until they are happy.

As I mentioned, the back end functionality is already there, just need design help. No coding required

Here is a link to the development page that they created: https://plumwickstudio.com/development/

As you can see, it looks off...doesnt line up properly, wasted space, weird font. Feel free to either correct the homepage they created or design an entirely new page. I am attaching some examples of before and after photos of artwork for reference. I also think the testimonials page and shop page can use a little style. The content is there and accurate, it just doesn't look pretty. Please keep in mind that our customers will probably not be very tech savvy. The customers will probably be sending us pics of kids, grandkids, pets, family portraits, vacation photos, etc.

Here is one of our competitors - www.gildavantry.com
Their website looks clean and inviting.

Thank you in advance! Im looking forward to seeing the results. I am including our logo in the attachments (I do not have it in a vector file, just a jpeg)

Target Market(s)

Non tech-savvy indiduals, 30-70 years old

Industry/Entity Type

Please look at https://plumwickstudio.com/development/ to see various pages and what the other designers did

Number of Pages Required

1 page

Requirements
Must have
• Verbiage on pages leave "as is" but feel free to change styles. Would like to keep existing four categories on homepage
Nice to have
• Warm and inviting homepage that evokes emotion

```html
<!DOCTYPE html>
<html lang="en">
<head>
<meta charset="utf-8">
<title>Brushfield Studio – Home</title>
<link href="https://fonts.googleapis.com/css2?family=Mulish:wght@400;600;700;800&family=Nunito:wght@900&display=swap" rel="stylesheet">
<style>
:root{
  --accent:#ee5a24;
  --ink:#111111;
  --body:#444444;
  --muted:#777777;
  --band:#f4f2f2;
  --footer:#141414;
  --line:#cfcfcf;
  --white:#ffffff;
}
*{box-sizing:border-box;margin:0;padding:0}
html,body{width:1200px;height:3855px;overflow:hidden}
body{position:relative;font-family:"Mulish",sans-serif;color:var(--body);background:var(--white)}
.abs{position:absolute}
.btn{position:absolute;display:flex;align-items:center;justify-content:center;background:var(--accent);color:var(--white);font-weight:800;font-size:14px;letter-spacing:.3px;text-transform:uppercase}
.section-title{position:absolute;left:0;width:1200px;text-align:center;font-weight:800;font-size:25px;color:var(--ink)}
.rule{position:absolute;width:34px;height:3px;background:var(--accent)}
.rule.center{left:583px}

.topbar{top:0;left:0;width:1200px;height:33px;background:#000;color:var(--white);font-size:13px;font-weight:600;display:flex;align-items:center;justify-content:center}
.brand{font-weight:800;font-size:26px;color:var(--ink);display:flex;align-items:center;gap:10px}
.brand .dot{width:22px;height:22px;border-radius:50%;background:var(--accent)}
.nav{top:72px;left:410px;display:flex;gap:31px;font-size:14.5px;color:var(--ink)}
.nav .active{color:var(--accent);border-bottom:1px solid var(--accent)}
.cart{left:1030px;top:66px}

.hero{left:133px;top:131px;width:935px;height:536px;background:radial-gradient(ellipse at 55% 45%,#d9c7ad 0%,#8a6a48 22%,#3f6a2c 45%,#2d4a1f 70%,#1c2e14 100%)}
.hero h1{position:absolute;left:58px;top:90px;font-family:"Nunito",sans-serif;font-weight:900;font-size:40px;line-height:44px;color:var(--white)}
.dots{left:568px;top:628px;display:flex;gap:9px}
.dots span{width:9px;height:9px;border-radius:50%;background:var(--white)}
.dots span.on{background:var(--accent)}

.cat-img{position:absolute;width:446px;height:313px}
.cat-label{position:absolute;font-size:19px;font-weight:700;color:var(--ink);width:300px;padding-bottom:10px;border-bottom:1px dotted #888}

.about-band{top:1629px;left:0;width:1200px;height:473px;background:var(--band)}
.about-text{left:619px;top:1754px;width:440px;font-size:13.3px;line-height:22px}
.about-text p+p{margin-top:18px}

.creation{position:absolute;top:2222px;width:300px;height:315px}
.chev{position:absolute;width:22px;height:22px}

.testi-band{top:2637px;left:0;width:1200px;height:527px;background:var(--band)}
.card{position:absolute;top:2768px;width:301px;height:344px;background:var(--white);border:1px solid #d6d6d6;text-align:center;padding:28px 32px 0}
.card .quote{font-family:"Nunito",sans-serif;font-weight:900;font-size:44px;color:var(--accent);line-height:40px;height:40px}
.card .stars{color:var(--accent);font-size:13px;letter-spacing:2px;margin-top:8px}
.card .words{font-size:12.5px;line-height:19.5px;margin-top:12px}
.card .sep{width:24px;height:1px;background:#bbb;margin:26px auto 22px}
.card .who{font-weight:800;color:var(--ink);font-size:13.5px}
.card .where{font-size:12.5px;margin-top:3px}

.why{position:absolute;top:3306px;width:300px;text-align:center}
.why .badge{width:120px;height:120px;border-radius:50%;background:#f1f1f1;margin:0 auto;display:flex;align-items:center;justify-content:center;box-shadow:-18px 0 0 -4px #f4b63a}
.why h3{font-size:17px;font-weight:700;color:var(--ink);margin-top:44px}
.why p{font-size:12.5px;line-height:19px;margin-top:14px;padding:0 28px}

.footer{top:3631px;left:0;width:1200px;height:224px;background:var(--footer);color:#ddd}
.footer .brand{color:var(--white);font-size:30px}
.foot-links{left:379px;top:3726px;display:flex;gap:12px;font-size:12.5px;color:#ddd}
.foot-links i{font-style:normal;color:#888}
.social{display:flex;gap:10px}
.social span{width:26px;height:26px;border-radius:50%;background:#4b6fb5}
</style>
</head>
<body>

<div class="abs topbar">FREE SHIPPING FOR ALL USA &nbsp;ORDERS</div>

<div class="abs brand" style="left:132px;top:64px"><span class="dot"></span>Brushfield Studio</div>
<nav class="abs nav">
  <span class="active">Home</span><span>Shop</span><span>Testimonials</span><span>About Us</span><span>FAQs</span><span>My Orders</span><span>Contact Us</span>
</nav>
<svg class="abs cart" width="30" height="30" viewBox="0 0 30 30">
  <path d="M2 6h4l3 13h14l3-9H8" fill="none" stroke="#111" stroke-width="2"/>
  <circle cx="11" cy="24" r="2" fill="#111"/><circle cx="21" cy="24" r="2" fill="#111"/>
  <circle cx="25" cy="6" r="6" fill="var(--accent)"/><text x="25" y="9" font-size="8" text-anchor="middle" fill="#fff" font-family="Mulish,sans-serif">0</text>
</svg>

<section class="abs hero" role="img" aria-label="Oil painting style portrait of a bride and groom among green ivy">
  <h1>Turn Your Digital<br>Photos Into<br>One of a Kind<br>Wall Art</h1>
  <div class="btn" style="left:63px;top:291px;width:171px;height:46px">Get Started</div>
</section>
<div class="abs dots"><span></span><span class="on"></span><span></span><span></span></div>

<h2 class="section-title" style="top:710px">CATEGORIES</h2>
<div class="rule center" style="top:753px"></div>

<div class="cat-img" style="left:132px;top:794px;background:linear-gradient(135deg,#c98a3e,#7a4a24 50%,#e2d8cc)" role="img" aria-label="Oil painting of a dog resting with an orange cat"></div>
<div class="cat-label" style="left:132px;top:1124px">Oil</div>
<div class="btn" style="left:446px;top:1128px;width:131px;height:34px">Get Started</div>

<div class="cat-img" style="left:619px;top:794px;background:linear-gradient(135deg,#f3ece8,#e3c3b3 50%,#faf7f5)" role="img" aria-label="Watercolor of a mother with her baby"></div>
<div class="cat-label" style="left:619px;top:1124px">Watercolor</div>
<div class="btn" style="left:934px;top:1128px;width:131px;height:34px">Get Started</div>

<div class="cat-img" style="left:132px;top:1200px;background:linear-gradient(180deg,#9fb6d6,#3fb6a5 45%,#c63a30 60%,#3a9c8a 80%,#b48a6a)" role="img" aria-label="Impressionist painting of a traveler by Venetian canals"></div>
<div class="cat-label" style="left:129px;top:1530px">Impressionist</div>
<div class="btn" style="left:446px;top:1534px;width:131px;height:34px">Get Started</div>

<div class="cat-img" style="left:619px;top:1200px;background:linear-gradient(180deg,#4d6b36,#8c8f72 50%,#a9a497)" role="img" aria-label="Photo of a father walking with a child on a forest path"></div>
<div class="cat-label" style="left:619px;top:1530px">Digital Photo</div>
<div class="btn" style="left:934px;top:1534px;width:131px;height:34px">Get Started</div>

<div class="abs about-band"></div>
<div class="abs" style="left:132px;top:1687px;width:436px;height:354px;background:linear-gradient(135deg,#e8ece4,#7f9a7c 50%,#6aa6c8)" role="img" aria-label="Painted portrait of a laughing older couple"></div>
<h2 class="abs" style="left:619px;top:1683px;font-size:25px;font-weight:800;color:var(--ink)">ABOUT US</h2>
<div class="rule" style="left:619px;top:1726px"></div>
<div class="abs about-text">
  <p>At Brushfield Studio, we take your digital photo and turn it into a one-of-a-kind piece of artwork!</p>
  <p>The process couldn't be any easier. Simply upload your photo, choose your art style and size, and let our team of skilled digital artists do the rest. Do you want to put your digital photo on canvas without an art style? No problem! Just choose the "Digital Photo/Retouching" category and upload your photo. We can print your photo "as is" or do some minor retouching (e.g. remove objects, enhance colors, lighten photo, etc)</p>
</div>
<div class="btn" style="left:619px;top:1998px;width:133px;height:37px">Read More</div>

<h2 class="section-title" style="top:2143px">RECENT CREATIONS</h2>
<div class="rule center" style="top:2192px"></div>
<svg class="chev" style="left:64px;top:2359px" viewBox="0 0 22 22"><path d="M15 2L6 11l9 9" fill="none" stroke="#999" stroke-width="2.5"/></svg>
<div class="creation" style="left:132px;background:linear-gradient(135deg,#3d5a2a,#8b3a2a 45%,#d8d0c2 70%,#8a8680)" role="img" aria-label="Finished canvas of a bride and groom shown beside the source photo"></div>
<div class="creation" style="left:450px;background:linear-gradient(180deg,#e8c66a,#7d8b8c 50%,#9a9488)" role="img" aria-label="Painted canvas of a father and child with the phone photo in hand"></div>
<div class="creation" style="left:769px;background:linear-gradient(135deg,#c27a2c,#6b4420 50%,#e6a24a)" role="img" aria-label="Painted canvas of a dog and cat with the phone photo in hand"></div>
<svg class="chev" style="left:1102px;top:2359px" viewBox="0 0 22 22"><path d="M7 2l9 9-9 9" fill="none" stroke="#999" stroke-width="2.5"/></svg>
<div class="btn" style="left:549px;top:2561px;width:103px;height:38px">View All</div>

<div class="abs testi-band"></div>
<h2 class="section-title" style="top:2674px">TESTIMONIALS</h2>
<div class="rule center" style="top:2722px"></div>
<svg class="chev" style="left:64px;top:2928px" viewBox="0 0 22 22"><path d="M15 2L6 11l9 9" fill="none" stroke="#999" stroke-width="2.5"/></svg>
<svg class="chev" style="left:1102px;top:2928px" viewBox="0 0 22 22"><path d="M7 2l9 9-9 9" fill="none" stroke="#999" stroke-width="2.5"/></svg>

<div class="card" style="left:132px">
  <div class="quote">&ldquo;</div><div class="stars">★★★★★</div>
  <p class="words">My mom is in an assisted living facility and has Alzheimers. We had a family portrait made into an oil and put in her room to help her remember us. The nurses always tell us how much she loves it and helps jog her memory. Thank you Brushfield Studio!</p>
  <div class="sep"></div><div class="who">Helen R</div><div class="where">Linden, MD</div>
</div>
<div class="card" style="left:449px">
  <div class="quote">&ldquo;</div><div class="stars">★★★★★</div>
  <p class="words">My mom is in an assisted living facility and has Alzheimers. We had a family portrait made into an oil and put in her room to help her remember us. The nurses always tell us how much she loves it and helps jog her memory. Thank you Brushfield Studio!</p>
  <div class="sep"></div><div class="who">Helen R</div><div class="where">Linden, MD</div>
</div>
<div class="card" style="left:767px">
  <div class="quote">&ldquo;</div><div class="stars">★★★★★</div>
  <p class="words">My mom is in an assisted living facility and has Alzheimers. We had a family portrait made into an oil and put in her room to help her remember us. The nurses always tell us how much she loves it and helps jog her memory. Thank you Brushfield Studio!</p>
  <div class="sep"></div><div class="who">Helen R</div><div class="where">Linden, MD</div>
</div>

<h2 class="section-title" style="top:3205px">WHY US?</h2>

<div class="why" style="left:98px">
  <div class="badge"><svg width="56" height="56" viewBox="0 0 56 56" fill="none" stroke="var(--accent)" stroke-width="2.5"><rect x="6" y="16" width="18" height="34"/><rect x="30" y="16" width="20" height="14"/><rect x="30" y="34" width="20" height="16"/><circle cx="15" cy="7" r="3"/></svg></div>
  <h3>Your Idea Your Design</h3>
  <p>Each art piece is customized for you! You choose your size, orientation and art style. Makes a perfect gift!!!</p>
</div>
<div class="why" style="left:448px">
  <div class="badge"><svg width="64" height="48" viewBox="0 0 64 48" fill="none" stroke="var(--accent)" stroke-width="2.5"><rect x="4" y="8" width="36" height="26"/><path d="M40 16h12l8 10v8H40z"/><circle cx="16" cy="38" r="5"/><circle cx="50" cy="38" r="5"/></svg></div>
  <h3>Fast Shipping</h3>
  <p>Your artwork is printed and shipped in the USA! We offer fast turnaround with transit times typically 3-7 days. Free tracking with each order!!</p>
</div>
<div class="why" style="left:804px">
  <div class="badge"><svg width="50" height="60" viewBox="0 0 50 60" fill="none" stroke="var(--accent)" stroke-width="2.5"><circle cx="25" cy="22" r="17"/><path d="M17 22l6 6 11-11"/><path d="M14 36l-6 20 9-5 5 8 3-14M36 36l6 20-9-5-5 8-3-14"/></svg></div>
  <h3>High Quality</h3>
  <p>We've put a lot of effort ensuring your artwork is of the highest quality. Each piece is printed on the highest quality, gallery grade canvas. It is ready to hang upon arrival.!</p>
</div>

<footer class="abs footer"></footer>
<div class="abs brand" style="left:132px;top:3690px;color:var(--white);font-size:28px"><span class="dot"></span>Brushfield Studio</div>
<svg class="abs" style="left:665px;top:3672px" width="28" height="20" viewBox="0 0 28 20" fill="none" stroke="#ddd" stroke-width="1.8"><rect x="1" y="1" width="26" height="18"/><path d="M1 1l13 10L27 1"/></svg>
<div class="abs" style="left:711px;top:3664px;font-size:13.5px;line-height:20px;color:#ddd">Email Us<br>info@brushfieldstudio.com</div>
<div class="abs" style="left:945px;top:3654px;font-size:13.5px;color:#ddd">Follow us</div>
<div class="abs social" style="left:945px;top:3678px"><span></span><span style="background:#5a7fb8"></span><span style="background:#333;border:1px solid #666"></span><span style="background:#d13a3a"></span></div>
<div class="abs foot-links"><span>About Us</span><i>|</i><span>My Orders</span><i>|</i><span>Testimonials</span><i>|</i><span>Get Started</span><i>|</i><span>FAQs</span><i>|</i><span>Privacy Policy</span><i>|</i><span>Terms and Conditions</span></div>
<div class="abs" style="left:132px;top:3770px;width:936px;height:1px;background:#333"></div>
<div class="abs" style="left:0;top:3804px;width:1200px;text-align:center;font-size:11px;color:#ddd">Copyright © 2023 All Rights Reserved</div>

</body>
</html>
```